Bold, Modern, Clean "Kestrelwaymassage.com" website

Why we stand out?
We are a male and female mobile massage team. Our names are Paul and Lina. 
Kestrel Way is a Seattle based mobile massage service. Our massage is offered to the community with a goal of facilitating balance within each individual. We specialize in integrated Pain management, and sports/medical massage therapy. Every client's first assessment is attended by our male and female massage therapist team. Depending on the goals identified for an individual determines which therapist will be assigned to provide treatment, if not both.

Our passion...
Here at Kestrel Way, we have a great passion for Postural Resoration and how it is integrated into an individual's Massage treatment. We pride ourselves in being natural facilitators of healing, which takes the ego of the therapist out of the client's healing process. We strive to deliver the best massage possible by including modalities such as Neuromuscular, Myofascial release, spontaneous muscle release, postural restoration, orthopedic, and medical massage.

Our education...

We are both Graduates of Venmora, school of massage therapy. We have continuing education in medical massage, myofacial release, trigger point therapy, postural restoration, anatomy, and spontaneous muscle release. Lina is also a Certified Yoga Instructor, which amplifies her experience with flexibility and strength as it pertains to each individual. Paul's passion is Massage, stretching, and strength training to encourage postural restoration and realignment.

Our rates-

Our rates are $75/ 60 minutes, $95/ 90 minutes, and $120/ 120 minutes.

Education-
Both Lina and I worked as behavioral health professionals that specialized in life skills mentoring for youth who had experienced different types of trauma. This led us both to want to help others in a different environment, where individuals can be empowered to take responsibility over their own healing. To us, massage is a type of manipulation physical therapy, that encourages healing on many levels.

Advice to any massage client-
The most important thing to 'us', as Licenced providers is to get you on to our table to show you our skills. But a good therapist never forgets that it's not about what we do for you, but what we can facilitate for you. Your health and healing has nothing to do with us. It is yours, not ours. Identify what your goals are with any Therapist, and know what the end looks like. Progress should be tangible, such as range of motion, and decreased pain.

Lina and Paul at Kestrel Way are awesome! I recently had open heart surgery, and Lina worked on me to increase my range of motion while helping with the pinched nerve from my arm being in the same position for so long during my surgery. My wife drives a lot for work, and Paul has helped decrease her neck and lower back pain immensely. They are seriously the best therapists I have ever worked with. I would recommend them to anyone who needs anything from stress relief to a medical massage treatment. They are professional, up beat, easy going, and always on time. And, I love that they meet us where ever we like! We did a staycation recently, where they came to our hotel to give us relaxation massages. Although usually they come to our home, where we focus on pain related issues. We will continue to work with them for a long, long time.

Target Market(s)

Mobile massage therapy clients

Industry/Entity Type

Massage Therapy

Coding

Coded - Design and coding required

Number of Pages Required

1 page

Font styles to use
Serif
Sans Serif

Requirements
Must have
• Please add or remove any information that would help the presentation of our website. Our logo is posted below, please include into the website.
• Please include a contact field that includes, kestrelwaymassage@fernmail.net,
• (206) 555-0148
• We have also included our own stock photos, as well as a photo of Paul and Lina. Please include a cropped photo of both massage therapists.

```html
<!DOCTYPE html>
<html lang="en">
<head>
<meta charset="utf-8">
<title>Kestrel Way – Mobile Massage</title>
<link href="https://fonts.googleapis.com/css2?family=Raleway:wght@300;400;500;600;700&family=Montserrat:wght@400;600;700&display=swap" rel="stylesheet">
<style>
:root{
  --teal:#06f2ca;
  --navy:#2740c4;
  --logo-blue:#1c3fd8;
  --ink:#2b2b2b;
  --muted:#555;
  --panel:#f4f4f4;
  --footer:#353535;
  --field:#5c5c5c;
  --field-line:#7a7a7a;
  --icon-dark:#4a4a4a;
  --white:#fff;
  --gold:#f3b22a;
}
*{box-sizing:border-box;margin:0;padding:0}
html,body{width:1200px;height:2667px;overflow:hidden;background:var(--white)}
body{font-family:'Raleway',sans-serif;color:var(--ink)}
.page{position:relative;width:1200px;height:2667px;overflow:hidden}
.abs{position:absolute}

/* hero */
.hero{left:0;top:0;width:1200px;height:654px;
  background:linear-gradient(180deg,#dcebf2 0%,#bcd6e4 35%,#9fbfd2 60%,#d9b9a6 80%,#b78f7c 100%)}
.nav a{position:absolute;top:72px;font-size:17px;letter-spacing:.3px;color:#333;text-decoration:none;text-transform:uppercase}
.nav a.active{color:var(--navy)}
.brand{position:absolute;left:530px;top:11px;width:142px;height:142px;border-radius:50%;
  background:var(--logo-blue);border:4px solid var(--white);display:flex;align-items:center;justify-content:center;
  text-align:center;color:var(--white);font-weight:700;font-size:24px;line-height:1.05}

/* welcome */
.welcome{left:0;top:654px;width:1200px;height:315px;background:var(--panel)}
.welcome h1{position:absolute;left:0;width:1200px;top:50px;text-align:center;font-weight:400;font-size:37px;color:#222}
.welcome p{position:absolute;left:311px;width:578px;top:116px;text-align:center;font-size:15px;line-height:25px;color:#555}
.btn-outline{position:absolute;border:1.5px solid #444;border-radius:26px;display:flex;align-items:center;justify-content:center;
  font-size:17px;text-transform:uppercase;color:#333;letter-spacing:.3px}
.read-more{left:523px;top:212px;width:154px;height:50px}
.portrait-lina{left:0;top:658px;width:311px;height:417px;background:linear-gradient(160deg,#7b5a4d,#c9a593 45%,#6f6e72);border-radius:0 0 40px 0}
.portrait-paul{left:884px;top:667px;width:289px;height:382px;background:linear-gradient(180deg,#b88c73,#2f52b8 40%,#2b2b2b 80%)}

/* services */
.services{left:0;top:969px;width:1200px;height:594px}
.services h2{position:absolute;left:0;width:1200px;top:176px;text-align:center;font-weight:400;font-size:37px;color:#222}
.faint-mark{left:119px;top:1036px;width:202px;height:202px;border-radius:50%;background:rgba(40,140,170,.25);
  display:flex;align-items:center;justify-content:center;color:rgba(255,255,255,.35);font-weight:700;font-size:34px;text-align:center;line-height:1.05}
.service-icon{position:absolute;width:142px;height:142px;border-radius:50%;border:3px solid var(--icon-dark);background:var(--white);padding:4px}
.service-icon .art{width:100%;height:100%;border-radius:50%;background:radial-gradient(circle at 50% 45%,#cfcfcf 0 38%,var(--icon-dark) 62%)}
.service-label{position:absolute;width:220px;text-align:center;font-size:18px;line-height:26px;color:#333}

/* testimonial */
.testimonial{left:0;top:1563px;width:1200px;height:414px;background:linear-gradient(90deg,#2c2a28,#4a4541 40%,#3a3633 65%,#252322)}
.testimonial h2{position:absolute;left:0;width:1200px;top:48px;text-align:center;font-weight:400;font-size:37px;color:var(--white)}
.testimonial h2 span{color:var(--teal)}
.stars{position:absolute;left:0;width:1200px;top:110px;text-align:center;color:var(--gold);font-size:22px;letter-spacing:1px}
.avatar{left:474px;top:1731px;width:90px;height:90px;border-radius:50%;border:3px solid var(--white);background:linear-gradient(160deg,#c9a790,#6e5a4c)}
.reviewer{position:absolute;left:590px;top:187px;font-size:20px;color:var(--teal)}
.review-date{position:absolute;left:590px;top:218px;font-size:15px;color:var(--white)}
.review{position:absolute;left:207px;width:786px;top:279px;text-align:center;font-size:15px;line-height:24px;color:var(--white)}
.arrow{position:absolute;top:200px}

/* call band */
.call{left:0;top:1977px;width:1200px;height:169px;background:var(--white)}
.phone-number{position:absolute;left:178px;top:49px;font-family:'Montserrat',sans-serif;font-weight:600;font-size:50px;color:#333}
.call-now{position:absolute;left:638px;top:57px;width:155px;height:50px;border:1.5px solid var(--navy);border-radius:26px;
  display:flex;align-items:center;justify-content:center;font-size:17px;color:var(--navy);text-transform:uppercase}
.device{left:870px;top:1945px;width:290px;height:150px;border-radius:22px;background:linear-gradient(135deg,#1b1b1b,#3a3a3a);transform:rotate(22deg);transform-origin:center}

/* footer */
.footer{left:0;top:2146px;width:1200px;height:521px;background:var(--footer)}
.stones{left:0;top:2134px;width:240px;height:284px;background:linear-gradient(160deg,#6d6d6d,#3e3e3e 40%,#c14fa8 65%,#2f7d34 90%)}
.sign-photo{left:0;top:2418px;width:626px;height:249px;background:linear-gradient(120deg,#eaeaea,#bfbfbf 40%,#7c6a55 70%,#3b5d2e)}
.contact-list{position:absolute;left:190px;top:2198px;list-style:none;color:#e6e6e6;font-size:17px}
.contact-list li{display:flex;align-items:center;height:36.5px}
.contact-list svg{width:18px;height:18px;margin-right:15px;flex:none}
.contact-title{position:absolute;left:251px;top:2338px;font-weight:300;font-size:40px;color:var(--teal);letter-spacing:.5px}
.field{position:absolute;left:521px;width:364px;background:var(--field);border:1.5px solid var(--field-line);color:#c9c9c9;font-size:13px;padding:16px 14px 0}
.send{position:absolute;left:761px;top:2489px;width:124px;height:52px;border:1.5px solid #ddd;color:var(--white);font-size:20px;display:flex;align-items:center;justify-content:center;text-transform:uppercase}
.footer-brand{left:967px;top:2210px;width:100px;height:100px;border-radius:50%;background:#e9e9e9;border:3px solid var(--white);
  display:flex;align-items:center;justify-content:center;text-align:center;color:#333;font-weight:700;font-size:17px;line-height:1.05}
.social{position:absolute;top:2354px;width:51px;height:50px;border:2px solid var(--teal)}
.social.filled{background:var(--teal)}
.copyright{position:absolute;left:650px;top:2624px;font-family:'Montserrat',sans-serif;font-weight:700;font-size:13px;color:var(--white)}
.copyright span{color:var(--teal)}
</style>
</head>
<body>
<div class="page">

  <section class="abs hero" role="img" aria-label="Photo of a woman relaxing during a head and neck massage by the sea"></section>
  <nav class="nav">
    <a href="#" class="active" style="left:197px">Home</a>
    <a href="#" style="left:286px">About</a>
    <a href="#" style="left:380px">Services</a>
    <a href="#" style="left:738px">Pricing</a>
    <a href="#" style="left:841px">Blog</a>
    <a href="#" style="left:926px">Contact</a>
  </nav>
  <div class="brand">KESTREL<br>WAY</div>

  <section class="abs welcome">
    <h1>Welcome To KESTREL WAY</h1>
    <p>Lorem Ipsum is simply dummy text of the printing and typesetting industry. Lorem Ipsum has been the industry's standard dummy text ever since the 1500s, when an unknown printer took a galley of type and scrambled it to.</p>
    <div class="btn-outline read-more">Read More</div>
  </section>
  <div class="abs portrait-lina" role="img" aria-label="Cropped photo of therapist Lina"></div>
  <div class="abs portrait-paul" role="img" aria-label="Cropped photo of therapist Paul crouching"></div>

  <section class="abs services">
    <svg class="abs" style="left:0;top:0" width="1200" height="594" viewBox="0 969 1200 594">
      <polygon points="0,1067 284,1017 1200,1218 1200,1484 0,1360" fill="var(--teal)"/>
    </svg>
    <h2>Our SERVICES</h2>
  </section>
  <div class="abs faint-mark">KESTREL<br>WAY</div>

  <div class="service-icon" style="left:78px;top:1293px"><div class="art" role="img" aria-label="Neuromuscular massage illustration"></div></div>
  <div class="service-label" style="left:39px;top:1445px">Neuromuscular</div>

  <div class="service-icon" style="left:256px;top:1236px"><div class="art" role="img" aria-label="Myofascial release illustration"></div></div>
  <div class="service-label" style="left:217px;top:1393px">Myofascial<br>Release</div>

  <div class="service-icon" style="left:432px;top:1293px"><div class="art" role="img" aria-label="Spontaneous muscle release illustration"></div></div>
  <div class="service-label" style="left:393px;top:1445px">Spontaneous<br>Muscle Release</div>

  <div class="service-label" style="left:583px;top:1239px">Postural<br>Restoration</div>
  <div class="service-icon" style="left:622px;top:1298px"><div class="art" role="img" aria-label="Postural restoration illustration"></div></div>

  <div class="service-label" style="left:761px;top:1315px">Orthopedic</div>
  <div class="service-icon" style="left:800px;top:1355px"><div class="art" role="img" aria-label="Orthopedic massage illustration"></div></div>

  <div class="service-label" style="left:937px;top:1239px">Medical<br>Massage</div>
  <div class="service-icon" style="left:976px;top:1298px"><div class="art" role="img" aria-label="Medical massage illustration"></div></div>

  <section class="abs testimonial" role="img" aria-label="Dimmed photo of a client receiving a massage">
    <h2><span>5/5 STARS</span> Massage Therapy</h2>
    <div class="stars">★★★★★</div>
    <svg class="arrow" style="left:390px" width="18" height="18" viewBox="0 0 18 18"><path d="M16 9H3M9 3L3 9l6 6" stroke="#fff" stroke-width="2.5" fill="none"/></svg>
    <svg class="arrow" style="left:793px" width="18" height="18" viewBox="0 0 18 18"><path d="M2 9h13M9 3l6 6-6 6" stroke="var(--teal)" stroke-width="2.5" fill="none"/></svg>
    <div class="reviewer">Darcy T.</div>
    <div class="review-date">December 17, 2015</div>
    <p class="review">Lina and Paul at Kestrel Way are awesome! I recently had open heart surgery, and Lina worked on me to increase my range of motion while helping with the pinched nerve from my arm being in the same position for so long during my surgery.</p>
  </section>
  <div class="abs avatar" role="img" aria-label="Reviewer photo"></div>

  <section class="abs call">
    <div class="phone-number">(206) 555-0148</div>
    <div class="call-now">Call Now</div>
  </section>
  <div class="abs device" role="img" aria-label="Smartphone showing the mobile site"></div>

  <footer class="abs footer"></footer>
  <div class="abs stones" role="img" aria-label="Photo of stacked massage stones with a pink orchid"></div>
  <div class="abs sign-photo" role="img" aria-label="Photo of a hand-painted wooden sign on a white building"></div>

  <ul class="contact-list">
    <li><svg viewBox="0 0 18 18"><path d="M9 1v16M3 4h10l2 2-2 2H3zM15 10H5l-2 2 2 2h10z" stroke="#e6e6e6" stroke-width="1.4" fill="none"/></svg>Alder Bay, Washington 98299</li>
    <li><svg viewBox="0 0 18 18"><path d="M4 1.5l3 3-2 2c1 2.5 3 4.5 5.5 5.5l2-2 3 3-2 3C7 15 3 11 1.5 4z" stroke="#e6e6e6" stroke-width="1.3" fill="none"/></svg>(206) 555-0148</li>
    <li><svg viewBox="0 0 18 18"><rect x="1" y="3.5" width="16" height="11" stroke="#e6e6e6" stroke-width="1.3" fill="none"/><path d="M1 3.5l8 6 8-6" stroke="#e6e6e6" stroke-width="1.3" fill="none"/></svg>kestrelwaymassage@fernmail.net</li>
  </ul>
  <div class="contact-title">CONTACT US</div>

  <div class="field" style="top:2199px;height:48px">Name</div>
  <div class="field" style="top:2261px;height:49px">E-Mail</div>
  <div class="field" style="top:2324px;height:153px">Message</div>
  <div class="send">Send</div>

  <div class="abs footer-brand">KESTREL<br>WAY</div>
  <div class="social filled" style="left:932px" aria-label="Social link"></div>
  <div class="social" style="left:994px" aria-label="Social link"></div>
  <div class="social" style="left:1056px" aria-label="Social link"></div>

  <div class="copyright">©2015 <span>KESTREL WAY</span>. All Rights Reserved</div>
</div>
</body>
</html>
```